Tech business card design

We need an amazing business card design for our new business 'Pexla' a marketing tech startup based in Sydney, Australia. We provide an online marketplace for businesses to search and buy advertising media, connect with service providers and learn more about marketing. We wish to communicate 'cool tech', reliability and professionalism and design based around our logo.

Target Market(s)

Business Owners

Contact Information for Business Card

Name
Position
Email Address
Website
Phone Number

Font styles to use
Other font styles liked:
• Avenir & Avenir Next

Colors

Designer to choose colors to be used in the design.

```html
<!DOCTYPE html>
<html lang="en">
<head>
<meta charset="utf-8">
<title>Pexla Business Card</title>
<link rel="stylesheet" href="https://fonts.googleapis.com/css2?family=Figtree:wght@400;600;700;800&display=swap">
<style>
  :root {
    --stage: #2a2a2e;
    --navy: #13133f;
    --white: #ffffff;
    --silver: #c9cad6;
    --ink: #1b1b4a;
    --divider: #9a9aa6;
  }
  * { margin: 0; padding: 0; box-sizing: border-box; }
  html, body {
    width: 1200px;
    height: 800px;
    overflow: hidden;
    background: var(--stage);
    font-family: "Figtree", "Avenir Next", sans-serif;
  }
  .stage {
    position: relative;
    width: 1200px;
    height: 800px;
  }
  .card {
    position: absolute;
    width: 520px;
    height: 298px;
    border-radius: 26px;
    overflow: hidden;
  }
  .card-front {
    left: 50px;
    top: 251px;
    background: var(--navy);
    display: flex;
    align-items: center;
    justify-content: center;
  }
  .card-back {
    left: 630px;
    top: 251px;
    display: flex;
    background: var(--navy);
  }
  .wordmark {
    font-weight: 800;
    letter-spacing: -2px;
    line-height: 1;
  }
  .card-front .wordmark {
    font-size: 120px;
    color: var(--silver);
  }
  .back-brand {
    width: 43%;
    background: var(--white);
    display: flex;
    align-items: center;
    justify-content: center;
    border-right: 3px solid var(--divider);
  }
  .back-brand .wordmark {
    font-size: 68px;
    color: var(--ink);
  }
  .back-details {
    flex: 1;
    color: var(--white);
    padding: 44px 26px 0 30px;
    font-size: 13.5px;
    line-height: 1.35;
  }
  .person-name {
    font-size: 20px;
    font-weight: 700;
    line-height: 1.1;
  }
  .person-role {
    font-size: 13.5px;
    margin-bottom: 16px;
  }
  .address { margin-bottom: 16px; }
  .contact-line {
    display: flex;
    align-items: center;
    gap: 8px;
  }
  .contact-line svg {
    width: 11px;
    height: 11px;
    fill: var(--white);
    flex-shrink: 0;
  }
  .website {
    margin-top: 16px;
    letter-spacing: 0.6px;
  }
  .website strong { font-weight: 700; }
</style>
</head>
<body>
<main class="stage">
  <section class="card card-front" aria-label="Card front">
    <span class="wordmark">pexla</span>
  </section>

  <section class="card card-back" aria-label="Card back">
    <div class="back-brand">
      <span class="wordmark">pexla</span>
    </div>
    <div class="back-details">
      <p class="person-name">Mara Quill</p>
      <p class="person-role">Manager</p>
      <p class="address">PO BOX 48, Harbour Lane<br>Sydney<br>Australia</p>
      <p class="contact-line">
        <svg viewBox="0 0 24 24" aria-hidden="true"><path d="M6.6 10.8a15.1 15.1 0 0 0 6.6 6.6l2.2-2.2a1 1 0 0 1 1-.25 11.4 11.4 0 0 0 3.6.57 1 1 0 0 1 1 1V20a1 1 0 0 1-1 1A17 17 0 0 1 3 4a1 1 0 0 1 1-1h3.5a1 1 0 0 1 1 1c0 1.25.2 2.45.57 3.57a1 1 0 0 1-.25 1z"/></svg>
        555.555.5555
      </p>
      <p class="contact-line">
        <svg viewBox="0 0 24 24" aria-hidden="true"><path d="M2 5h20v14H2z M2 5l10 8 10-8" fill="none" stroke="#fff" stroke-width="2.4"/></svg>
        hello@pexlamedia.com
      </p>
      <p class="website">www.<strong>pexlamedia</strong>.com</p>
    </div>
  </section>
</main>
</body>
</html>
```